Quorva - corporate Business Card

We need a good look and innovative business card for a new start up company based in Los Angeles called "Quorva". We are in a payment business, including payment card, app, and ewallet. We are expert in online payment and Card not present (CNP) transaction.
We need an innovative, modern business card.

Our logo font is Aero Matics

Target Market(s)

Startup - Bank - Online Payment - Card Manufacturing

Industry/Entity Type

Startup

Contact Information for Business Card

phone: 555 014 7396 - Address: 4172 Marlowe blvd, Larkmont, CA 90299

Requirements
Must have
• Message: innovative, professional, expert, high tech, trust, online payment expert, security
Nice to have
• no comment
Should not have
• no Comment

```html
<!DOCTYPE html>
<html lang="en">
<head>
<meta charset="utf-8">
<title>Quorva – Business Card</title>
<link href="https://fonts.googleapis.com/css2?family=Lato:wght@400;700&display=swap" rel="stylesheet">
<style>
  :root {
    --backdrop: #5b5b5b;
    --card-light: #fafafa;
    --card-dark: #111111;
    --brand-red: #b5202e;
    --ink: #1a1a1a;
  }
  html, body {
    margin: 0;
    padding: 0;
    width: 1200px;
    height: 900px;
    overflow: hidden;
    background: var(--backdrop);
    font-family: "Lato", Arial, sans-serif;
  }
  .canvas {
    position: relative;
    width: 1200px;
    height: 900px;
  }
  .card {
    position: absolute;
    top: 192px;
    height: 491px;
    border-radius: 14px;
    overflow: hidden;
  }
  .card-front {
    left: 295px;
    width: 301px;
    background: var(--card-light);
    border-radius: 0 14px 14px 0;
    text-align: center;
    color: var(--ink);
  }
  .card-back {
    left: 621px;
    width: 305px;
    background: var(--card-dark);
  }
  .front-mark {
    position: absolute;
    left: 72px;
    top: 50px;
    width: 156px;
    height: 156px;
    border-radius: 50%;
    background: var(--brand-red);
    color: #ffffff;
    display: flex;
    align-items: center;
    justify-content: center;
    font-size: 30px;
    font-weight: 700;
    letter-spacing: 0.5px;
  }
  .holder {
    position: absolute;
    left: 0;
    right: 0;
    top: 263px;
  }
  .holder-name {
    margin: 0;
    color: var(--brand-red);
    font-size: 19px;
    font-weight: 700;
    letter-spacing: 0.6px;
    line-height: 24px;
  }
  .holder-role {
    margin: 0;
    font-size: 14px;
    line-height: 20px;
    letter-spacing: 0.4px;
  }
  .divider {
    width: 136px;
    height: 1px;
    margin: 10px auto 7px;
    background: linear-gradient(90deg, rgba(181,32,46,0), rgba(181,32,46,0.75), rgba(181,32,46,0));
  }
  .divider-lower {
    margin: 6px auto 7px;
  }
  .contact-line {
    margin: 0;
    font-size: 15px;
    line-height: 20px;
  }
  .address {
    margin: 0;
    font-size: 15px;
    line-height: 18px;
  }
  .back-brand {
    position: absolute;
    left: 29px;
    top: 208px;
    display: flex;
    align-items: center;
    gap: 10px;
  }
  .back-brand-dot {
    width: 74px;
    height: 74px;
    border-radius: 50%;
    background: var(--brand-red);
  }
  .back-brand-name {
    color: var(--brand-red);
    font-size: 46px;
    font-weight: 700;
    letter-spacing: 1px;
    line-height: 1;
    padding-bottom: 6px;
  }
</style>
</head>
<body>
  <main class="canvas">
    <section class="card card-front">
      <div class="front-mark">Quorva</div>
      <div class="holder">
        <p class="holder-name">MARK DELANO</p>
        <p class="holder-role">DIRECTOR</p>
        <div class="divider"></div>
        <p class="contact-line">555 014 7396</p>
        <p class="contact-line">www.quorva.com</p>
        <div class="divider divider-lower"></div>
        <p class="address">4172 Marlowe blvd,<br>Larkmont, CA 90299</p>
      </div>
    </section>
    <section class="card card-back">
      <div class="back-brand">
        <span class="back-brand-dot"></span>
        <span class="back-brand-name">quorva</span>
      </div>
    </section>
  </main>
</body>
</html>
```